TalbeckLabs needs a new rocket based website

We need a new website that will be based on our rocket ship logo. We develop innovative solutions for enterprises. We would like to see a design that when the pages scroll, the rocket launches and goes from launch through a journey, similar to how we approach our customer. We would like areas for "Who are we", "What can we do", "What have we done", "How can we help". http://www.talbecklabs.example.au is our current website

Target Market(s)

Government, Enterprise, Cloud

Industry/Entity Type

Software Service

Coding

Coded - Design and coding required

Number of Pages Required

2 page

Requirements
Must have
• We would like to see a design that when the pages scroll, the rocket launches and goes from launch through a journey, similar to how we approach our customer.
• Must have a home page and a detail page.
• Would like to see the logo/rocket animate in some way when you scroll through he page.

```html
<!DOCTYPE html>
<html lang="en">
<head>
<meta charset="utf-8">
<title>TalbeckLabs</title>
<link rel="stylesheet" href="https://fonts.googleapis.com/css2?family=Montserrat:wght@400;500;600;700&family=Open+Sans:wght@400;600&display=swap">
<style>
:root{
  --orange:#f7941d;
  --orange-light:#fbb04f;
  --sky-top:#12a6e3;
  --sky-bottom:#47b9ec;
  --ink:#333;
  --muted:#555;
  --grey-band:#f4f4f4;
  --card-head:#3a3a3a;
  --line:#dcdcdc;
  --white:#fff;
}
*{box-sizing:border-box;margin:0;padding:0}
html,body{width:1200px;height:4675px;overflow:hidden;background:var(--white)}
body{font-family:"Montserrat",sans-serif;color:var(--ink);position:relative}
.abs{position:absolute}

/* hero */
.hero{position:absolute;left:0;top:0;width:1200px;height:1060px;background:linear-gradient(180deg,var(--sky-top),var(--sky-bottom) 80%);overflow:hidden}
.brand{position:absolute;left:40px;top:50px;font-weight:700;font-size:30px;color:var(--orange);display:flex;align-items:center;gap:10px}
.brand .dot{width:16px;height:16px;border-radius:50%;background:var(--orange)}
.nav{position:absolute;right:40px;top:58px;display:flex;gap:38px}
.nav a{color:var(--white);text-decoration:none;font-size:17px;font-weight:500}
.hero-rocket{position:absolute;left:280px;top:90px;width:230px;height:880px;border-radius:110px 110px 20px 20px;background:linear-gradient(180deg,#f7a43a,#f38a1c 40%,#fbd08a 80%,rgba(255,255,255,.6))}
.hero-title{position:absolute;left:555px;top:308px;width:560px;color:var(--white);font-weight:700;font-size:35px;line-height:50px}
.hero-sub{position:absolute;left:555px;top:545px;width:510px;color:var(--white);font-size:22px;line-height:34px;font-weight:400}
.btn-start{position:absolute;left:555px;top:655px;width:287px;height:56px;border-radius:28px;background:var(--white);color:var(--sky-top);font-weight:600;font-size:20px;display:flex;align-items:center;justify-content:center}
.cloud-band{position:absolute;left:0;top:920px;width:1200px;height:140px;background:linear-gradient(180deg,rgba(255,255,255,0),rgba(255,255,255,.85) 45%,var(--white))}

/* section titles */
.section-title{position:absolute;left:0;width:1200px;display:flex;justify-content:center;align-items:center;gap:14px;font-size:31px;font-weight:600;color:var(--ink)}
.section-title .dot{width:18px;height:18px;border-radius:50%;background:var(--orange)}

/* services */
.art{position:absolute;border-radius:24px}
.svc-title{position:absolute;font-size:40px;color:var(--orange);font-weight:400;white-space:nowrap}
.svc-text{position:absolute;font-size:20px;line-height:30px;color:var(--muted);width:430px}

/* work */
.work{position:absolute;left:0;top:2696px;width:1200px;height:645px;background:var(--grey-band)}
.card{position:absolute;top:2914px;width:485px;height:337px;background:var(--white);border-radius:8px;box-shadow:0 4px 14px rgba(0,0,0,.15);overflow:hidden}
.card-head{height:78px;background:var(--card-head);color:var(--white);display:flex;align-items:center;justify-content:center;gap:14px;font-size:19px;letter-spacing:1px}
.card-head .seal{width:44px;height:44px;border-radius:50%;background:#777}
.card-body{padding:22px 28px 0;text-align:center;font-family:"Open Sans",sans-serif;font-size:15px;line-height:22px;color:var(--ink)}
.card-sub{color:var(--orange);font-weight:700;font-family:"Montserrat",sans-serif;font-size:18px;margin:10px 0 12px;padding-bottom:10px;border-bottom:1px solid var(--line)}
.features{display:grid;grid-template-columns:1fr 1fr;row-gap:10px;text-align:left;font-size:13px}
.features span{display:flex;align-items:center;gap:8px}
.features i{width:16px;height:16px;border-radius:3px;background:#1f3f73;flex:none}
.features span:nth-child(even) i{background:var(--orange)}
.slide-arrow{position:absolute;top:3050px;width:30px;height:60px;background:var(--white);display:flex;align-items:center;justify-content:center}

/* contact */
.field{position:absolute;height:47px;border:1px solid var(--line);background:var(--white);font-family:"Open Sans",sans-serif;font-size:14px;padding:12px 14px;color:var(--ink);font-weight:600}
.btn-send{position:absolute;left:477px;top:3756px;width:243px;height:44px;border-radius:22px;background:var(--orange);color:var(--white);font-weight:600;font-size:20px;display:flex;align-items:center;justify-content:center}
.map{position:absolute;left:0;top:3890px;width:1200px;height:427px;background:linear-gradient(135deg,#eceae6,#e2e0dc)}

/* footer */
.footer{position:absolute;left:0;top:4317px;width:1200px;height:303px;background:var(--orange);color:var(--white)}
.footer .brand{left:94px;top:74px;color:var(--white);font-size:32px}
.footer .brand .dot{background:var(--white)}
.f-col{position:absolute;top:60px;font-size:14px;line-height:22px}
.f-col h4{font-size:14px;font-weight:700;letter-spacing:.5px;padding-bottom:10px;margin-bottom:12px;border-bottom:1px solid rgba(255,255,255,.6);width:160px}
.f-col li{list-style:none;display:flex;align-items:center;gap:8px}
.f-email{width:260px;height:32px;border-radius:16px;background:var(--white);color:#777;font-size:13px;padding:7px 16px;margin-top:12px}
.f-sub{width:130px;height:30px;border-radius:15px;background:#333;color:var(--white);font-size:13px;font-weight:700;display:flex;align-items:center;justify-content:center;margin-top:12px}
.copyright{position:absolute;left:0;top:4620px;width:1200px;height:55px;background:var(--orange-light);display:flex;align-items:center;justify-content:center;font-size:13px;font-weight:600;color:#333}
</style>
</head>
<body>

<header class="hero">
  <div class="brand"><span class="dot"></span>TalbeckLabs</div>
  <nav class="nav">
    <a href="#">Who Are We</a><a href="#">What Can We Do</a><a href="#">What Have We Done</a><a href="#">How Can We Help</a>
  </nav>
  <div class="hero-rocket" role="img" aria-label="Illustrated orange rocket launching with exhaust trail"></div>
  <h1 class="hero-title">Offering the latest in<br>enterprise architecture,<br>design and development<br>of bespoke software solutions</h1>
  <p class="hero-sub">Always researching and implementing<br>the latest technology for customers.</p>
  <div class="btn-start">Get Started</div>
  <div class="cloud-band" role="img" aria-label="Illustrated white clouds at the base of the launch"></div>
</header>

<h2 class="section-title" style="top:1212px"><span class="dot"></span>What Can We Do</h2>

<div class="art" style="left:125px;top:1340px;width:311px;height:280px;border-radius:50%;background:radial-gradient(circle,#4fc1c8,#1fa2a8)" role="img" aria-label="Illustration of a laptop showing a parliament voting screen"></div>
<h3 class="svc-title" style="left:517px;top:1408px">e-Parliament</h3>
<p class="svc-text" style="left:517px;top:1475px;width:420px">All of your Parliamentary software and business process needs.</p>

<h3 class="svc-title" style="left:280px;top:1735px">Cloud</h3>
<p class="svc-text" style="left:280px;top:1800px;width:360px">Cloud Office Suites, Migration, Security, Customisations.</p>
<div class="art" style="left:670px;top:1636px;width:296px;height:328px;background:linear-gradient(160deg,#3fa6f0,#b9a6ef)" role="img" aria-label="Isometric illustration of a cloud server workstation"></div>

<div class="art" style="left:140px;top:1948px;width:312px;height:327px;background:linear-gradient(150deg,#fde9d1,#e7eef7)" role="img" aria-label="Illustration of a person riding a rocket among charts"></div>
<h3 class="svc-title" style="left:517px;top:2056px">Architecture &amp; Design</h3>
<p class="svc-text" style="left:517px;top:2125px;width:420px">Business process design, technology strategy and architecture.</p>

<h3 class="svc-title" style="left:156px;top:2380px">Software Development</h3>
<p class="svc-text" style="left:156px;top:2447px;width:380px">Software development including business apps, web and mobile.</p>
<div class="art" style="left:670px;top:2291px;width:296px;height:343px;background:linear-gradient(150deg,#5b7fe8,#f4b6c7)" role="img" aria-label="Illustration of people building a dashboard with charts"></div>

<section class="work"></section>
<h2 class="section-title" style="top:2802px"><span class="dot"></span>What Have We Done</h2>

<div class="slide-arrow" style="left:0;border-radius:0 6px 6px 0"><svg width="14" height="22" viewBox="0 0 14 22"><path d="M11 3 L3 11 L11 19" fill="none" stroke="#f7941d" stroke-width="4"/></svg></div>
<div class="slide-arrow" style="right:0;border-radius:6px 0 0 6px"><svg width="14" height="22" viewBox="0 0 14 22"><path d="M3 3 L11 11 L3 19" fill="none" stroke="#f7941d" stroke-width="4"/></svg></div>

<article class="card" style="left:100px">
  <div class="card-head"><span class="seal"></span>PARLIAMENT of ALDERIA</div>
  <div class="card-body">
    <p>Lorem ipsum dolor sit amet, consectetur adipiscing elit, sed do eiusmod tempor incididunt ut labore.</p>
    <p class="card-sub">Work Done</p>
    <div class="features">
      <span><i></i>Access Mobile Internet</span><span><i></i>Alert via SMS, Email &amp; App</span>
      <span><i></i>Video &amp; Rich Media Articles</span><span><i></i>Social Advocacy &amp; Sharing</span>
      <span><i></i>Teams &amp; Groups</span><span><i></i>Business Design &amp; Tech</span>
    </div>
  </div>
</article>
<article class="card" style="left:614px">
  <div class="card-head">PARLIAMENT OF NORTH VALE</div>
  <div class="card-body">
    <p>Lorem ipsum dolor sit amet, consectetur adipiscing elit, sed do eiusmod tempor incididunt ut labore.</p>
    <p class="card-sub">Work Done</p>
    <div class="features">
      <span><i></i>Access Mobile Internet</span><span><i></i>Alert via SMS, Email &amp; App</span>
      <span><i></i>Video &amp; Rich Media Articles</span><span><i></i>Social Advocacy &amp; Sharing</span>
      <span><i></i>Teams &amp; Groups</span><span><i></i>Business Design &amp; Tech</span>
    </div>
  </div>
</article>

<h2 class="section-title" style="top:3447px"><span class="dot"></span>How Can We Help</h2>
<div class="field" style="left:115px;top:3544px;width:315px">Your Name</div>
<div class="field" style="left:452px;top:3544px;width:305px">Your Email</div>
<div class="field" style="left:773px;top:3544px;width:312px">Your Subject</div>
<div class="field" style="left:115px;top:3609px;width:970px;height:131px">Message</div>
<div class="btn-send">Send</div>

<div class="map" role="img" aria-label="Street map showing the office location">
  <svg class="abs" style="left:585px;top:170px" width="30" height="42" viewBox="0 0 30 42" aria-hidden="true"><path d="M15 0 C6 0 0 7 0 15 C0 26 15 42 15 42 C15 42 30 26 30 15 C30 7 24 0 15 0Z" fill="#e74c3c"/><circle cx="15" cy="15" r="5" fill="#9b1c12"/></svg>
</div>

<footer class="footer">
  <div class="brand"><span class="dot"></span>TalbeckLabs</div>
  <div class="f-col" style="left:355px">
    <h4>QUICK LINKS</h4>
    <ul><li>› Who We Are</li><li>› What Can We Do</li><li>› What Have We Done</li><li>› How Can We Help</li></ul>
  </div>
  <div class="f-col" style="left:583px">
    <h4>CONTACT</h4>
    <ul>
      <li><svg width="16" height="16" viewBox="0 0 16 16"><circle cx="8" cy="8" r="7" fill="none" stroke="#fff" stroke-width="1.5"/><circle cx="8" cy="7" r="2.5" fill="#fff"/></svg>TalbeckLabs</li>
      <li style="padding-left:24px">Unit 3, 14 Kestrel Rd</li>
      <li style="padding-left:24px">Marlow SA 5999</li>
      <li style="margin-top:14px"><svg width="16" height="16" viewBox="0 0 16 16"><circle cx="8" cy="8" r="7" fill="none" stroke="#fff" stroke-width="1.5"/><path d="M5 4 L7 6 L6 8 L8 10 L10 9 L12 11 L10 12 Q6 12 4 7 Z" fill="#fff"/></svg>1300 000 123</li>
      <li style="margin-top:10px"><svg width="16" height="16" viewBox="0 0 16 16"><circle cx="8" cy="8" r="7" fill="none" stroke="#fff" stroke-width="1.5"/><rect x="4" y="5" width="8" height="6" fill="none" stroke="#fff"/><path d="M4 5 L8 8 L12 5" fill="none" stroke="#fff"/></svg>info@talbecklabs.example.au</li>
    </ul>
  </div>
  <div class="f-col" style="left:851px">
    <h4 style="width:260px">NEWSLETTER SUBSCRIPTION</h4>
    <p style="width:260px">Register your email address to get more information about us</p>
    <div class="f-email">Email Address</div>
    <div class="f-sub">SUBSCRIBE</div>
  </div>
</footer>
<div class="copyright">COPYRIGHT © 2018 TALBECKLABS. ALL RIGHTS RESERVED.</div>

</body>
</html>
```